Flyer, poster, banner and social media titles designs for Community Mending Chartre

The Harbourline Charter for Community Mending provide a nationally agreed framework to guide recovery policy and practice across Australia. The Principles support recovery practitioners, governments, non-government organisations and communities to deliver effective, community-centred recovery outcomes.
The Principles have recently been refreshed through extensive consultation and we require a contemporary visual identity and design suite that will increase awareness, engagement and practical application of the Principles.
The redesign will cover:
• A4 Brochure (primary publication)
• A3 Poster
• Pull up banner
• Social Media Tiles
The new design should:
• Create a recognisable brand for the Harbourline Charter.
• Appeal to both experienced and emerging recovery practitioners.
• Reflect contemporary Community Mending practice.
• Feel people-focused rather than government-focused.
• Support future resources such as videos, implementation guides, presentations and workshop materials.
• Remain relevant for several years without requiring a major redesign.
Target Audience
• Community Mending practitioners
• Government agencies
• Non-government organisations
• Community recovery workers
• Recovery managers and leaders
• Community stakeholders and volunteers
The visual identity should reflect the six Principles:
• Understanding Context
• Recognising Complexity
• Community-Centred Approaches
• Coordination
• Communication
• Capacity Building
The design should communicate:
• Recovery is centred on people and communities.
• Recovery is collaborative and involves many sectors.
• Recovery is adaptive, inclusive and evidence-informed.
• Recovery supports resilience and long-term wellbeing.
• The Principles provide practical guidance for recovery practice.
We are looking for:
• Modern and professional
• Warm and approachable
• Human-centred
• Inclusive and accessible
• Australian in context
• Visually engaging
• Suitable for print and digital use
We would like to avoid:
• Images of disaster destruction
• Emergency response imagery (fire trucks, flashing lights, etc.)
• Overly corporate or bureaucratic designs
• Designs that focus on deficits rather than recovery and growth
Consider themes such as:
• Connection and collaboration
• Communities and people
• Growth, recovery and renewal
Accessibility
Designs should:
• Meet accessibility best practice
• Use clear typography
• Achieve strong colour contrast
• Be suitable for both digital and print formats

Deliverables
1. Principles Brochure
• A4 trifold size x 2 (online and print friendly version)
• A side to include cover side, logos side and overview of principles.
• B side full details of the principles
• Graphic to highlight the 3 c’s concept (RECOVERY Context, complexity, community centred, coordinate, communicate and capacity). Currently 3 circles.
• Can be printed and distributed electronically
2. Poster
• A1 and A3 versions
• Suitable for office and workshop display
3. Pull-Up Banner - 850 mm (W) × 2000 mm (H)
• Conference and event use
• High visual impact
• Strong branding and concise messaging
4. Social Media Tiles x 3

We are providing an extension and increasing the budget following feedback from designers. We are wanting the resources to look and feel different from the existing designs, considering either a different colour palette in the designs or different motif with the leave design. Any nature based designs should consider the Australian fauna or flora. Also suggest avoiding images in the designs. The principles are not numbered or liner in the concept of how they function. Happy to answer any further questions and thank you for your suggested concepts.

Community Mending practitioners, Government agencies , Non-government organisations, Community recovery workers and Community stakeholders and volunteers

Community Mending

• Modern, warm, visually engaging, human-centred, Australian in context and different to the current design.
• Symbols for each principles
• Images of disaster destruction, Emergency response imagery, Overly corporate or bureaucratic designs, Designs that focus on deficits rather than recovery and growth, avoid too much black

```html
<!DOCTYPE html>
<html lang="en">
<head>
<meta charset="utf-8">
<title>Harbourline Charter for Community Mending – Trifold Brochure</title>
<link rel="stylesheet" href="https://fonts.googleapis.com/css2?family=Libre+Baskerville:wght@400;700&family=Poppins:wght@400;500;600&display=swap">
<style>
  :root{
    --bg:#d9d9d9;
    --kraft:#d8c3a2;
    --cream:#eee2ce;
    --paper:#f5efe5;
    --green:#4f9a34;
    --ink:#2c2a27;
    --muted:#5b5247;
    --line:#8b8178;
    --badge:#fbf9f5;
    --fill-seedling:#6f8048;
    --fill-family:#b7a78e;
    --fill-people:#a88c74;
    --fill-tree:#9aa3ab;
    --fill-diagram:#d8e4ec;
    --serif:"Libre Baskerville", Georgia, serif;
    --sans:"Poppins", Arial, sans-serif;
  }
  *{box-sizing:border-box;margin:0;padding:0}
  html,body{width:1200px;height:900px;overflow:hidden;background:var(--bg)}
  body{position:relative;font-family:var(--sans);color:var(--ink)}

  .sheet{position:absolute;top:243px;width:585px;height:414px;display:flex;box-shadow:0 2px 8px rgba(0,0,0,.15)}
  .sheet--outer{left:10px}
  .sheet--inner{left:605px}
  .panel{position:relative;width:195px;height:100%;overflow:hidden}
  .panel + .panel{border-left:1px solid rgba(0,0,0,.06)}

  .image-area{position:absolute;border-radius:50%}

  /* outer side */
  .overview{background:var(--kraft);padding:14px 12px 0 14px}
  .kicker{font-size:4.6px;font-weight:600;letter-spacing:.3px;text-transform:uppercase}
  .overview h2{font-family:var(--serif);font-size:10px;font-weight:700;letter-spacing:.4px;line-height:1.1;margin:1px 0 4px}
  .overview h2 span{color:var(--green);font-weight:400}
  .intro{font-size:4.4px;line-height:1.45;color:var(--muted);width:150px}
  .timeline{list-style:none;margin:8px 0 0 6px;border-left:1px solid var(--line);padding-left:8px;width:160px}
  .timeline li{position:relative;margin-bottom:5px}
  .timeline li::before{content:"";position:absolute;left:-11px;top:1px;width:5px;height:5px;border-radius:50%;background:var(--green)}
  .timeline h3{font-family:var(--serif);font-size:5.3px;font-weight:400;letter-spacing:.2px;text-transform:uppercase;margin-bottom:1px}
  .timeline p{font-size:4.3px;line-height:1.4;color:var(--muted)}
  .timeline li.short p{width:70px}
  .principles-diagram{left:100px;bottom:8px;width:78px;height:78px;background:var(--fill-diagram)}

  .partners{background:var(--cream)}
  .seedling{left:38px;top:30px;width:118px;height:118px;background:var(--fill-seedling)}
  .badges{position:absolute;left:20px;top:176px;width:140px;display:grid;grid-template-columns:repeat(3,34px);gap:6px 10px;justify-content:center}
  .badges span{width:34px;height:34px;border-radius:50%;background:var(--badge);box-shadow:0 0 0 1px rgba(0,0,0,.05)}
  .partners-label{position:absolute;left:14px;top:340px;font-size:5.6px;font-weight:500;letter-spacing:.4px;text-transform:uppercase;line-height:1.3}
  .rule{position:absolute;left:16px;top:196px;width:1px;height:120px;background:var(--ink)}

  .cover{background:var(--cream)}
  .family{left:40px;top:-12px;width:178px;height:178px;background:var(--fill-family)}
  .lines{position:absolute;left:14px;top:176px;width:28px}
  .lines i{display:block;height:1px;background:var(--line);margin-bottom:2.5px}
  .cover-title{position:absolute;left:20px;top:226px;width:170px}
  .cover-title .kicker{font-size:5.4px}
  .cover-title h1{font-family:var(--serif);font-weight:700;font-size:19px;line-height:1.05;letter-spacing:.5px;margin-top:3px}
  .cover-title h1 span{display:block;color:var(--green);font-weight:400;font-size:18px}

  /* inner side */
  .principles{display:flex;gap:6px;padding:12px 8px 0}
  .principles--kraft{background:var(--kraft)}
  .principles--cream{background:var(--cream)}
  .col{width:87px;position:relative}
  .col h2{font-family:var(--serif);font-size:6.6px;font-weight:400;line-height:1.1;letter-spacing:.3px;text-transform:uppercase;min-height:22px}
  .col h2 span{display:block;color:var(--green)}
  .col .lead{font-size:4.2px;line-height:1.4;color:var(--muted);margin:3px 0 5px}
  .head-band{position:absolute;left:0;right:0;top:0;height:70px;background:var(--paper)}
  .points{list-style:none;border-left:1px solid var(--line);margin-left:3px;padding-left:6px}
  .points li{position:relative;font-size:4.1px;line-height:1.38;color:var(--muted);margin-bottom:4px}
  .points li::before{content:"";position:absolute;left:-8.5px;top:.5px;width:4px;height:4px;border-radius:50%;background:var(--green)}
  .people{left:-14px;bottom:-18px;width:96px;height:86px;background:var(--fill-people)}
  .tree{left:-10px;bottom:-30px;width:90px;height:90px;background:var(--fill-tree)}
</style>
</head>
<body>

<section class="sheet sheet--outer" aria-label="Brochure outer side">

  <article class="panel overview">
    <p class="kicker">Harbourline Charter for</p>
    <h2>Community <span>Mending</span></h2>
    <p class="intro">Disasters can deeply impact lives and livelihoods. Working with communities recovering from disasters is complex and challenging. Recovery is a long-term, non-linear and dynamic process. These principles are a way to guide our efforts, our approach, our planning and our decision-making. Recovery is part of emergency management, which includes the broader components of prevention, preparedness and response, and can provide an opportunity to improve wellbeing beyond previous conditions.</p>
    <ul class="timeline">
      <li><h3>Understand the Context</h3><p>Successful recovery is based on an understanding of the community context, with each community having its own history, values and dynamics.</p></li>
      <li><h3>Recognise Complexity</h3><p>Successful recovery is responsive to the complex and evolving nature of disasters and their impacts on communities, including compounding, cascading and concurrent events.</p></li>
      <li><h3>Use Community-Centred Approaches</h3><p>Successful recovery is community-centred, responsive and flexible, engaging with community and supporting them to move forward, with shared responsibilities.</p></li>
      <li><h3>Coordinate All Activities</h3><p>Successful recovery requires a planned, coordinated and adaptive approach, between community and partner agencies, based on continuing assessment of impacts and needs.</p></li>
      <li><h3>Communicate Effectively</h3><p>Successful recovery is built on effective communication between the affected community and other partners.</p></li>
      <li class="short"><h3>Recognise and<br>Build Capacity</h3><p>Successful recovery recognises, supports and builds on individual, community and organisational capacity and resilience.</p></li>
    </ul>
    <div class="image-area principles-diagram" role="img" aria-label="Circular diagram of the six principles around community mending"></div>
  </article>

  <article class="panel partners">
    <div class="image-area seedling" role="img" aria-label="Photograph of a young seedling growing from mossy ground"></div>
    <div class="badges" aria-label="Partner badges">
      <span></span><span></span><span></span>
      <span></span><span></span><span></span>
      <span></span><span></span><span></span>
      <span></span><span></span><span></span>
    </div>
    <span class="rule"></span>
    <p class="partners-label">Partners in development<br>from the</p>
  </article>

  <article class="panel cover">
    <div class="image-area family" role="img" aria-label="Photograph of a family together outdoors on green grass"></div>
    <div class="lines"><i></i><i></i><i></i><i></i><i></i><i></i></div>
    <div class="cover-title">
      <p class="kicker">Harbourline Charter for</p>
      <h1>Community <span>Mending</span></h1>
    </div>
  </article>
</section>

<section class="sheet sheet--inner" aria-label="Brochure inner side">

  <article class="panel principles principles--kraft">
    <div class="col">
      <h2>Understand <span>the context</span></h2>
      <p class="lead">Successful recovery is based on an understanding of the community context, with each community having its own history, values and dynamics. Recovery should:</p>
      <ul class="points">
        <li>Acknowledge existing strengths and capacity, including past experiences and aspirations;</li>
        <li>Appreciate the risks and stressors faced by the community;</li>
        <li>Embed accessibility, equity, inclusion and diversity in recovery practice;</li>
        <li>Support people who may be at greater risk or disproportionately impacted;</li>
        <li>Respect and support connections to Country and culturally significant places;</li>
        <li>Recognise pathways and timeframes vary with community needs;</li>
        <li>Acknowledge the impact may extend beyond the disaster area.</li>
      </ul>
    </div>
    <div class="col">
      <h2>Recognise <span>complexity</span></h2>
      <p class="lead">Successful recovery is responsive to the complex and evolving impacts on communities. Recovery should recognise that:</p>
      <ul class="points">
        <li>Disasters lead to a range of effects that require a variety of approaches;</li>
        <li>Information on impacts and needs can be limited at first and changes over time;</li>
        <li>Affected individuals have diverse needs, wants and expectations;</li>
        <li>Responsive and flexible action is crucial to addressing immediate needs;</li>
        <li>Existing community knowledge may challenge the assumptions of those outside;</li>
        <li>Conflicting values and priorities may create tensions;</li>
        <li>Emergencies create stressful settings where grief may affect those involved;</li>
        <li>Over time, support for individuals and communities builds hope and growth.</li>
      </ul>
    </div>
    <div class="image-area people" role="img" aria-label="Photograph of community members talking together"></div>
  </article>

  <article class="panel principles principles--cream">
    <div class="head-band"></div>
    <div class="col">
      <h2>Use community centred <span>approaches</span></h2>
      <p class="lead">Successful recovery is community-centred, engaging with community and supporting them to move forward. Recovery should:</p>
      <ul class="points">
        <li>Assist and enable individuals, families and community to participate in their own recovery;</li>
        <li>Recognise that people may need different support at various times;</li>
        <li>Be guided by the communities' priorities;</li>
        <li>Channel effort through existing community assets and leadership;</li>
        <li>Build partnerships that reflect diverse representation;</li>
        <li>Support Aboriginal and Torres Strait Islander self-determination;</li>
        <li>Recognise that new community leaders often emerge;</li>
        <li>Recognise that communities may choose different paths.</li>
      </ul>
    </div>
    <div class="col">
      <h2>Coordinate <span>all activities</span></h2>
      <p class="lead">Successful recovery requires a planned and adaptive approach between community and partner agencies. Recovery should:</p>
      <ul class="points">
        <li>Have clearly shared goals based on desired outcomes;</li>
        <li>Be flexible, taking into account changes in community needs;</li>
        <li>Be guided by those with experience and expertise;</li>
        <li>Be at the pace desired by the community;</li>
        <li>Reflect well-developed community planning;</li>
        <li>Have clear decision-making and reporting structures;</li>
        <li>Demonstrate an understanding of roles across agencies;</li>
        <li>Be inclusive, building upon relationships created before.</li>
      </ul>
    </div>
    <div class="image-area tree" role="img" aria-label="Photograph of a bare tree standing in still water"></div>
  </article>

  <article class="panel principles principles--cream">
    <div class="head-band"></div>
    <div class="col">
      <h2>Communicate <span>effectively</span></h2>
      <p class="lead">Successful recovery is built on effective communication between the affected community and other partners. Recovery should:</p>
      <ul class="points">
        <li>Recognise that communication should be two-way, transparent and ongoing;</li>
        <li>Ensure information is accessible to audiences in diverse situations;</li>
        <li>Establish mechanisms for coordinated and consistent communications;</li>
        <li>Ensure all communication is relevant, timely, clear, accurate and credible;</li>
        <li>Identify trusted sources and repeat key recovery messages to build confidence.</li>
      </ul>
    </div>
    <div class="col">
      <h2>Recognise and <span>build capacity</span></h2>
      <p class="lead">Successful recovery builds on individual, community and organisational capacity and resilience. Recovery should:</p>
      <ul class="points">
        <li>Assess capability and capacity before, during and after a disaster;</li>
        <li>Support self-reliance, preparation and disaster mitigation;</li>
        <li>Quickly mobilise community skills, strengths and resources;</li>
        <li>Develop networks and partnerships to strengthen capacity;</li>
        <li>Support training and knowledge sharing;</li>
        <li>Ensure mental health and wellbeing supports are available;</li>
        <li>Understand when and how to step back;</li>
        <li>Monitor, evaluate and capture learning to build resilience.</li>
      </ul>
    </div>
  </article>
</section>

</body>
</html>
```